New business card for a regional office of a US M&A company

We need business card for a finance company, office based in Hong Kong , our Head office is in US, our business is to Merge and acquires companies , the new office will be a regional office for the Asia Pacific region. We want to use the head office logo as attached ( but don't have to be exactly the same, can be a variation to it) as a base and then add Asia Pacific alongside the logo.
We would prefer to have be bilingual Eng + Chinese, although we don't really have Chinese company name .

Industry/Entity Type

Business

Contact Information for Business Card

Clara Jo Tsang
 

VP,
APAC M&A Operations
Orin Vantage Asia Pacific Limited
 
Unit 1407, K18
18 Tai Lok Shan Road, 
Hong Kong 
 
M: +852 6038 1742
T : +852 2836 4100
F : +852 2836 4177
VOIP: 4158
 
cjtsang@orinvantage.com

Font styles to use
Serif
Sans Serif

Colors

Designer to choose colors to be used in the design.

Requirements
Must have
• APAC Office

```html
<!DOCTYPE html>
<html lang="en">
<head>
<meta charset="utf-8">
<title>Orin Vantage – Business Card</title>
<link href="https://fonts.googleapis.com/css2?family=Roboto:wght@400;700&family=Roboto+Condensed:wght@700&display=swap" rel="stylesheet">
<style>
  :root {
    --backdrop: #e9e7e4;
    --cyan: #1eabd0;
    --navy: #0f2942;
    --white: #ffffff;
    --strip: #f1f3f5;
    --url: #c9d3dc;
  }
  * { margin: 0; padding: 0; box-sizing: border-box; }
  html, body { width: 1200px; height: 960px; overflow: hidden; }
  body {
    position: relative;
    background: var(--backdrop);
    font-family: "Roboto", Arial, sans-serif;
  }
  .card {
    position: absolute;
    height: 343px;
    box-shadow: 2px 3px 6px rgba(0,0,0,0.35);
    overflow: hidden;
  }
  .card-front { left: 314px; top: 113px; width: 600px; background: var(--strip); }
  .card-back  { left: 311px; top: 472px; width: 601px; background: var(--navy); }

  .contact-panel {
    position: absolute; left: 0; top: 0; width: 278px; height: 100%;
    background: var(--cyan); color: var(--white);
    padding: 57px 0 0 36px;
  }
  .brand-panel {
    position: absolute; left: 278px; top: 0; width: 307px; height: 100%;
    background: var(--navy);
  }
  .holder-name {
    font-family: "Roboto Condensed", "Arial Narrow", sans-serif;
    font-weight: 700; font-size: 20px; line-height: 24px; letter-spacing: 0.2px;
  }
  .holder-title { font-size: 14px; line-height: 20px; margin: 0 0 7px 3px; }
  .office-lines { font-size: 14px; line-height: 19px; }
  .phone-list { list-style: none; margin-top: 7px; font-size: 14px; line-height: 19px; }
  .phone-list li { display: flex; align-items: center; }
  .phone-list svg { width: 14px; height: 14px; margin-right: 8px; fill: var(--white); }
  .voip { font-size: 14px; line-height: 19px; margin-top: 9px; }

  .brand-mark {
    position: absolute; left: 0; right: 0;
    display: flex; align-items: center; justify-content: center; gap: 12px;
    color: var(--cyan); font-family: "Roboto", Arial, sans-serif; font-weight: 700;
    white-space: nowrap;
  }
  .brand-square { background: var(--cyan); flex: none; }
  .brand-panel .brand-mark { top: 195px; font-size: 30px; }
  .brand-panel .brand-square { width: 22px; height: 22px; }
  .card-back .brand-mark { top: 185px; font-size: 46px; gap: 16px; }
  .card-back .brand-square { width: 34px; height: 34px; }

  .web-address {
    position: absolute; left: 0; right: 0; top: 284px;
    text-align: center; color: var(--url);
    font-size: 14px; letter-spacing: 5px;
  }
</style>
</head>
<body>

<section class="card card-front">
  <div class="contact-panel">
    <p class="holder-name">CLARA JO TSANG</p>
    <p class="holder-title">VP</p>
    <p class="office-lines">
      APAC M&amp;A Operations<br>
      Orin Vantage Asia Pacific Limited<br>
      Unit 1407, K18<br>
      18 Tai Lok Shan Road<br>
      Hong Kong
    </p>
    <ul class="phone-list">
      <li><svg viewBox="0 0 24 24" aria-hidden="true"><path d="M6.6 10.8a15.1 15.1 0 0 0 6.6 6.6l2.2-2.2c.3-.3.7-.4 1-.2 1.1.4 2.3.6 3.6.6.6 0 1 .4 1 1V20c0 .6-.4 1-1 1A17 17 0 0 1 3 4c0-.6.4-1 1-1h3.5c.6 0 1 .4 1 1 0 1.3.2 2.5.6 3.6.1.3 0 .7-.2 1z"/></svg>+852 2836 4100</li>
      <li><svg viewBox="0 0 24 24" aria-hidden="true"><path d="M7 1h10a2 2 0 0 1 2 2v18a2 2 0 0 1-2 2H7a2 2 0 0 1-2-2V3a2 2 0 0 1 2-2zm0 3v14h10V4zm5 15.5a1 1 0 1 0 0 2 1 1 0 0 0 0-2z"/></svg>+852 6038 1742</li>
      <li><svg viewBox="0 0 24 24" aria-hidden="true"><path d="M6 2h10v5H6zM3 8h18a2 2 0 0 1 2 2v8h-3v4H4v-4H1v-8a2 2 0 0 1 2-2zm3 8v4h12v-4zm12-5a1 1 0 1 0 0 2 1 1 0 0 0 0-2z"/></svg>+852 2836 4177</li>
    </ul>
    <p class="voip">VOIP: 4158</p>
  </div>
  <div class="brand-panel">
    <div class="brand-mark"><span class="brand-square"></span>ORIN VANTAGE</div>
  </div>
</section>

<section class="card card-back">
  <div class="brand-mark"><span class="brand-square"></span>ORIN VANTAGE</div>
  <p class="web-address">www.orinvantage.com</p>
</section>

</body>
</html>
```